International Manufacturing Business Needs A Heavy Hitting Wordpress Design!

We need wordpress template designs for a new website for our UK based International company Dalvesham Engineering Ltd. We manufacture and supply steel security doors and window units. We would like designs that feature the black and yellow industrial "stripes" that can be seen at our current site www.dalvoportals.com. The final design should communicate strength, power and weight to represent the quality of the products and the security that they provide.

It feels like we need 3 different types of page to be able to be created as per the current website at www.dalvosafeportals.com.

Homepage
Products/Accessories
Leadtimes/Downloads/Contact

It may be that 3 different page types can be created with one template. I'm totally open to this.

I don't like the way that the site currently handles product images, nobody wants to click on even thumbnail to see the product. http://dalvosafeportals.com/products/personnel-doors/

Totally open to suggestions on layout to enable the feeling outlined in the brief above.

Please ask if anything is not clear or you need answers to drill down on specifics.

Sick

Target Market(s)

Businesses that buy steel doors

Font styles to use
Sans Serif
Other font styles liked:
• Copperplate Gothic Bold - For Company Name but we are open to suggestions

Colors

Designer to choose colors to be used in the design.

Requirements
Must have
• Professional looking, clean design
• Conveys strength, power and weight to represent the quality of the products, the characteristics of steel and the security that they provide.
• Incorporates black and yellow stripes of our branding
• Ability to create pages with content as seen at www.dalvosafeportals.com
• A better way of showing the product images
Nice to have
• If possible. a design that gives off the feeling that not only do we supply the products we also make them in house too. I don't know what this looks like but a way of differentiating between a supply only business and one that manufacturers the product too.
Should not have
• We don't like the current thumbnail method of showing the product images

```html
<!DOCTYPE html>
<html lang="en">
<head>
<meta charset="utf-8">
<title>Dalvesham Engineering Ltd</title>
<link rel="stylesheet" href="https://fonts.googleapis.com/css2?family=Open+Sans:wght@400;600;700;800&display=swap">
<style>
:root{
  --yellow:#d4d20a;
  --yellow-deep:#8f9a00;
  --gold:#e9b71b;
  --ink:#141414;
  --dark:#1c1c1a;
  --text:#333;
  --muted:#555;
  --white:#fff;
  --rule:#cfcfcf;
  --photo-grey:#c7c3bb;
  --photo-blue:#c3cfda;
  --photo-white:#ececec;
  --photo-sand:#e2d5c4;
}
*{margin:0;padding:0;box-sizing:border-box}
html,body{width:1200px;height:3488px;overflow:hidden;background:var(--white)}
body{position:relative;font-family:"Open Sans",Arial,sans-serif;color:var(--text)}
.abs{position:absolute}

/* hero */
.hero{left:0;top:0;width:1200px;height:650px}
.site-header{left:0;top:0;width:1200px;height:115px;background:linear-gradient(#0f0f0d,rgba(15,15,13,.75));}
.brand{left:98px;top:22px;display:flex;align-items:center;gap:12px}
.brand-mark{width:40px;height:40px;background:var(--white);flex:none}
.brand-name{color:var(--white);font-weight:700;font-size:21px;line-height:1;letter-spacing:.3px;white-space:nowrap}
.topbar{top:26px;color:var(--white);font-size:14px;display:flex;align-items:center;gap:8px;white-space:nowrap}
.order-btn{left:960px;top:22px;width:150px;height:36px;background:var(--yellow);border:2px solid #a8a400;color:#111;font-size:13px;font-weight:700;display:flex;align-items:center;justify-content:center}
.nav{top:78px;display:flex;color:var(--white);font-size:14px}
.nav a{position:absolute;color:inherit;text-decoration:none;white-space:nowrap}
.hero-title{left:84px;top:216px;color:var(--white);font-size:46px;font-weight:800;letter-spacing:.5px}
.hero-sub{left:84px;top:288px;width:640px;color:var(--white);font-size:21px;font-weight:600;line-height:31px}
.btn{display:flex;align-items:center;justify-content:center;font-size:17px;font-weight:600;color:var(--white)}
.btn-solid{left:84px;top:384px;width:214px;height:58px;background:linear-gradient(var(--yellow),var(--yellow-deep))}
.btn-ghost{left:326px;top:384px;width:211px;height:58px;border:2px solid var(--white)}

/* what we do */
.work-photo{left:84px;top:780px;width:435px;height:430px}
.wwd-title{left:605px;top:772px;font-size:36px;font-weight:800;color:var(--ink)}
.wwd-list{left:605px;top:830px;width:500px;list-style:none;font-size:11.5px;line-height:26px;color:var(--muted)}
.wwd-list li{position:relative;padding-left:16px;margin-bottom:2px}
.wwd-list li::before{content:"";position:absolute;left:0;top:8px;width:10px;height:10px;border-radius:50%;background:var(--yellow)}
.read-more{left:607px;top:1175px;width:121px;height:42px;background:linear-gradient(var(--yellow),var(--yellow-deep));color:var(--white);font-size:15px;font-weight:700;display:flex;align-items:center;justify-content:center}

/* about */
.about-bg{left:0;top:1350px}
.about-title{left:0;top:1540px;width:1200px;text-align:center;color:var(--white);font-size:34px;font-weight:800}
.about-intro{left:200px;top:1604px;width:800px;text-align:center;color:var(--white);font-size:13px;line-height:26px}
.feature{width:340px;text-align:center;color:var(--white)}
.feature-icon{position:relative;margin:0 auto;width:98px;height:98px;border:3px solid var(--gold);border-radius:50%;display:flex;align-items:center;justify-content:center}
.feature-num{position:absolute;left:8px;top:-12px;width:30px;height:30px;border-radius:50%;background:var(--gold);color:var(--white);font-size:14px;font-weight:700;display:flex;align-items:center;justify-content:center}
.feature h3{margin-top:22px;font-size:21px;font-weight:700}
.feature p{margin-top:8px;font-size:13px;line-height:26px}

/* products */
.section-title{left:0;top:2222px;width:1200px;display:flex;justify-content:center;align-items:center;gap:24px;font-size:31px;font-weight:800;color:var(--ink)}
.section-title::before,.section-title::after{content:"";width:95px;height:1px;background:var(--rule)}
.product{width:244px}
.product-photo{height:228px;border:1px solid #ddd;box-shadow:0 2px 6px rgba(0,0,0,.15)}
.product-name{margin-top:16px;text-align:center;font-size:20px;color:var(--text)}
.chev{font-size:30px;color:#444}

/* testimonials */
.testimonials{left:0;top:2714px;width:1200px;height:426px;background:linear-gradient(160deg,#2a2a22,#101010 60%,#1e1c10)}
.t-title{left:0;top:2800px;width:1200px;text-align:center;color:var(--white);font-size:31px;font-weight:800}
.avatar{left:126px;top:2862px;width:190px;height:190px;border-radius:50%;border:8px solid var(--yellow);background:radial-gradient(circle at 50% 45%,#c9a58c,#6b4a34)}
.quote{left:423px;top:2885px;width:690px;color:var(--white);font-size:13px;line-height:27px}
.quote b{font-size:26px;line-height:0;vertical-align:-6px;margin:0 6px}
.t-name{left:426px;top:2986px;color:var(--white);font-size:15px;font-weight:700;letter-spacing:.5px}
.stars{left:424px;top:3018px}

/* footer */
.f-head{top:3220px;font-size:17px;font-weight:600;color:#222}
.f-text{font-size:12.5px;line-height:28px;color:#444}
.social{top:3340px;display:flex;gap:10px;left:84px}
.social span{width:32px;height:32px;border:1.5px solid #222;border-radius:50%}
.f-contact{left:503px;top:3258px;font-size:12.5px;line-height:26px;color:#444}
.f-contact div{display:flex;gap:12px}
.f-contact svg{flex:none;margin-top:7px}
.subscribe{left:803px;top:3318px;width:300px;height:36px;border:1.5px solid #222;border-radius:18px;display:flex;align-items:center;justify-content:space-between;padding:0 16px 0 22px;font-size:12.5px;color:#444}
.f-rule{left:84px;top:3434px;width:1032px;height:1px;background:var(--rule)}
.copyright{left:0;top:3450px;width:1200px;text-align:center;font-size:12px;color:#444}
</style>
</head>
<body>

<!-- hero -->
<svg class="abs hero" width="1200" height="650" viewBox="0 0 1200 650" role="img" aria-label="Photograph of a fitter kneeling on a workbench drilling into a white door panel">
  <defs>
    <linearGradient id="heroFill" x1="0" y1="0" x2="1" y2="1">
      <stop offset="0" stop-color="#6a5a46"/>
      <stop offset=".45" stop-color="#a89274"/>
      <stop offset="1" stop-color="#4b3d2e"/>
    </linearGradient>
  </defs>
  <polygon points="0,0 1200,0 1200,600 0,590" fill="url(#heroFill)"/>
  <polygon points="0,590 1200,600 1200,640 0,595" fill="var(--yellow)"/>
  <polygon points="0,595 1200,640 1200,650 0,650" fill="#fff"/>
  <polyline points="22,312 38,330 22,348" fill="none" stroke="#fff" stroke-width="5"/>
  <polyline points="1174,312 1158,330 1174,348" fill="none" stroke="#fff" stroke-width="5"/>
</svg>

<header class="abs site-header">
  <div class="abs brand"><span class="brand-mark"></span><span class="brand-name">Dalvesham Engineering Ltd</span></div>
  <div class="abs topbar" style="left:582px">
    <svg width="14" height="14" viewBox="0 0 24 24"><path fill="#fff" d="M6.6 10.8a15 15 0 0 0 6.6 6.6l2.2-2.2c.3-.3.7-.4 1-.2 1.1.4 2.3.6 3.6.6.6 0 1 .4 1 1V20c0 .6-.4 1-1 1A17 17 0 0 1 3 4c0-.6.4-1 1-1h3.5c.6 0 1 .4 1 1 0 1.3.2 2.5.6 3.6.1.3 0 .7-.2 1z"/></svg>
    +44 (0)1632 960 418
  </div>
  <div class="abs topbar" style="left:766px">
    <svg width="16" height="12" viewBox="0 0 16 12"><rect width="16" height="12" fill="#fff"/><polyline points="0,0 8,7 16,0" fill="none" stroke="#222" stroke-width="1.4"/></svg>
    sales@dalvoportals.com
  </div>
  <div class="abs order-btn">Online Order Form</div>
  <nav class="abs nav" style="left:0">
    <a style="left:526px">Home</a>
    <a style="left:591px">Products</a>
    <a style="left:672px">Accessories</a>
    <a style="left:772px">Delivery &amp; lead times</a>
    <a style="left:928px">Downloads</a>
    <a style="left:1023px">Contact</a>
    <svg style="position:absolute;left:1100px;top:3px" width="14" height="14" viewBox="0 0 14 14"><circle cx="5.5" cy="5.5" r="4" fill="none" stroke="#fff" stroke-width="2"/><line x1="8.5" y1="8.5" x2="13" y2="13" stroke="#fff" stroke-width="2.4"/></svg>
  </nav>
</header>

<h1 class="abs hero-title">RIGHT STYLE FOR YOU</h1>
<p class="abs hero-sub">Create the room of your Dream with a security doors combine a high level of security with exceptional value.</p>
<div class="abs btn btn-solid">More Information</div>
<div class="abs btn btn-ghost">View Our Products</div>

<!-- what we do -->
<svg class="abs work-photo" width="435" height="430" viewBox="0 0 435 430" role="img" aria-label="Photograph of hands fitting a lock into a wooden door edge">
  <defs>
    <linearGradient id="workFill" x1="0" y1="0" x2="1" y2="1">
      <stop offset="0" stop-color="#6d6257"/>
      <stop offset=".5" stop-color="#d8c7ad"/>
      <stop offset="1" stop-color="#b79c80"/>
    </linearGradient>
  </defs>
  <path d="M0 0H435V405Q220 330 0 430Z" fill="url(#workFill)"/>
  <path d="M0 430Q220 330 435 405V430Z" fill="#111"/>
  <path d="M0 430Q220 320 435 400V410Q220 335 0 430Z" fill="var(--yellow)"/>
</svg>
<h2 class="abs wwd-title">WHAT WE DO...</h2>
<ul class="abs wwd-list">
  <li>Dalvesham security doors combine a high level of security with exceptional value.</li>
  <li>Our superior quality and proven reliability has made us the first choice for a wide range of companies no matter what their requirement or application.</li>
  <li>All of our products are designed and manufactured to the highest specification, combine this with a rigorous quality control system and an extensive after-sales service and it is easy to see why we are seen as industry leaders.</li>
  <li>We place particular emphasis on continuous development and twelve years experience ensures that we are always ahead of the competition and that we can react quickly to customer's requirements.</li>
  <li>Each and every Dalvesham product is subject to our fifty point quality control process before it is dispatched.</li>
  <li>Dalvesham have forged a reputation for affordable, high quality steel doors.</li>
</ul>
<div class="abs read-more">Read More</div>

<!-- about -->
<svg class="abs about-bg" width="1200" height="800" viewBox="0 0 1200 800" role="img" aria-label="Dark workshop photograph of tools behind the about section">
  <defs>
    <linearGradient id="aboutFill" x1="0" y1="0" x2="1" y2="1">
      <stop offset="0" stop-color="#1b1b1b"/>
      <stop offset=".5" stop-color="#2a2723"/>
      <stop offset="1" stop-color="#121212"/>
    </linearGradient>
  </defs>
  <polygon points="0,150 1200,0 1200,640 0,785" fill="url(#aboutFill)"/>
  <polygon points="0,30 600,180 0,200" fill="var(--yellow)"/>
  <polygon points="1200,580 1200,730 600,685" fill="var(--yellow)"/>
</svg>
<h2 class="abs about-title">ABOUT US</h2>
<p class="abs about-intro">We place particular emphasis on continuous development and twelve years experience ensures that we are always ahead of the competition and that we can react quickly to customer's requirements.</p>

<div class="abs feature" style="left:56px;top:1698px">
  <div class="feature-icon"><span class="feature-num">1</span>
    <svg width="38" height="30" viewBox="0 0 38 30" fill="#fff"><circle cx="19" cy="8" r="6"/><path d="M8 28c0-7 5-11 11-11s11 4 11 11z"/><circle cx="7" cy="11" r="4"/><circle cx="31" cy="11" r="4"/><path d="M0 25c0-5 3-8 7-8 2 0 3 .5 4 1-2 2-3 4-3 7zM38 25c0-5-3-8-7-8-2 0-3 .5-4 1 2 2 3 4 3 7z"/></svg>
  </div>
  <h3>Experienced Team</h3>
  <p>Lorem Ipsum is simply dummy text of the printing and typesetting industry.</p>
</div>
<div class="abs feature" style="left:428px;top:1698px">
  <div class="feature-icon"><span class="feature-num">2</span>
    <svg width="34" height="32" viewBox="0 0 34 32"><path d="M4 20V16a13 13 0 0 1 26 0v4" fill="none" stroke="#fff" stroke-width="4"/><rect x="2" y="18" width="8" height="13" rx="3" fill="#fff"/><rect x="24" y="18" width="8" height="13" rx="3" fill="#fff"/></svg>
  </div>
  <h3>Service support</h3>
  <p>Lorem Ipsum is simply dummy text of the printing and typesetting industry.</p>
</div>
<div class="abs feature" style="left:798px;top:1698px">
  <div class="feature-icon"><span class="feature-num">3</span>
    <svg width="32" height="32" viewBox="0 0 32 32" fill="#fff"><rect x="1" y="13" width="7" height="17"/><path d="M10 14l7-12c3 0 4 2 3 5l-1 5h9c2 0 3 2 3 3l-3 13c-.5 2-2 2-3 2H10z"/></svg>
  </div>
  <h3>Quality Products</h3>
  <p>Lorem Ipsum is simply dummy text of the printing and typesetting industry.</p>
</div>

<!-- products -->
<h2 class="abs section-title">OUR PRODUCTS</h2>
<span class="abs chev" style="left:32px;top:2404px">&#8249;</span>
<span class="abs chev" style="left:1158px;top:2404px">&#8250;</span>
<div class="abs product" style="left:84px;top:2314px">
  <div class="product-photo" role="img" aria-label="Product photograph of washroom cubicle doors" style="background:var(--photo-grey)"></div>
  <div class="product-name">Personal Door</div>
</div>
<div class="abs product" style="left:344px;top:2314px">
  <div class="product-photo" role="img" aria-label="Product photograph of a fire exit door" style="background:var(--photo-blue)"></div>
  <div class="product-name">Fire Exit Door</div>
</div>
<div class="abs product" style="left:607px;top:2314px">
  <div class="product-photo" role="img" aria-label="Product photograph of a plain white door" style="background:var(--photo-white)"></div>
  <div class="product-name">Blank Door</div>
</div>
<div class="abs product" style="left:868px;top:2314px">
  <div class="product-photo" role="img" aria-label="Product photograph of a wooden acoustic door" style="background:var(--photo-sand)"></div>
  <div class="product-name">Acoustic Door</div>
</div>

<!-- testimonials -->
<section class="abs testimonials"></section>
<h2 class="abs t-title">TESTIMONIALS</h2>
<div class="abs avatar" role="img" aria-label="Portrait photograph of the client"></div>
<p class="abs quote"><b>&ldquo;</b>Aliquam dictum elit vitae mauris facilisis, at dictum urna dignissim. Donec vel lectus vel felis lacinia luctus vitae tow iaculis arcu. Mauris mattis, massa eu porta ultricies. Aliquam dictum elit vitae metj jolkas lijl kalsa adda pougpd teo hoas ada aff afggeppu lpi jpjuhis auris facilisis, at dictum urna dignissim.<b>&rdquo;</b></p>
<div class="abs t-name">MARA QUENTLEY</div>
<svg class="abs stars" width="108" height="20" viewBox="0 0 108 20" fill="#fff">
  <g id="star"><polygon points="10,1 12.6,7 19,7.4 14,11.6 15.6,18 10,14.5 4.4,18 6,11.6 1,7.4 7.4,7"/></g>
  <use href="#star" x="21"/><use href="#star" x="42"/><use href="#star" x="63"/>
  <polygon points="94,1 94,14.5 88.4,18 90,11.6 85,7.4 91.4,7"/>
  <polygon points="94,1 96.6,7 103,7.4 98,11.6 99.6,18 94,14.5" fill="none" stroke="#fff" stroke-width="1.2"/>
</svg>

<!-- footer -->
<h3 class="abs f-head" style="left:84px">About</h3>
<p class="abs f-text" style="left:84px;top:3256px;width:330px">Duis autem velaeum iriure dolor in hendrerit in vulpu tate velit esse molestie consequat, vel illum dolore eu feugiat vel eum iriure dolor in hendrerit.</p>
<div class="abs social"><span></span><span></span><span></span><span></span></div>

<h3 class="abs f-head" style="left:503px">Contact</h3>
<div class="abs f-contact">
  <div><svg width="10" height="13" viewBox="0 0 10 13"><path d="M5 0a5 5 0 0 1 5 5c0 3-5 8-5 8S0 8 0 5a5 5 0 0 1 5-5z" fill="#222"/><circle cx="5" cy="5" r="1.8" fill="#fff"/></svg><span>Dalvesham Engineering Ltd.<br>Marrow Hill, Fenwick Lane,<br>Holmbrook, Hull UK. HU99 4ZZ</span></div>
  <div><svg width="12" height="9" viewBox="0 0 12 9"><rect width="12" height="9" fill="#222"/><polyline points="0,0 6,5 12,0" fill="none" stroke="#fff" stroke-width="1"/></svg><span>sales@dalvoportals.com</span></div>
  <div><svg width="11" height="11" viewBox="0 0 24 24"><path fill="#222" d="M6.6 10.8a15 15 0 0 0 6.6 6.6l2.2-2.2c.3-.3.7-.4 1-.2 1.1.4 2.3.6 3.6.6.6 0 1 .4 1 1V20c0 .6-.4 1-1 1A17 17 0 0 1 3 4c0-.6.4-1 1-1h3.5c.6 0 1 .4 1 1 0 1.3.2 2.5.6 3.6.1.3 0 .7-.2 1z"/></svg><span>+44 (0)1632 960 418</span></div>
</div>

<h3 class="abs f-head" style="left:803px">Subscribe To Newsletter</h3>
<p class="abs f-text" style="left:803px;top:3256px;width:320px">Hendrerit vulputate velit esse molestie soluta consafg bxf esaev quat vellilum nobis.</p>
<div class="abs subscribe">Your Email Address
  <svg width="18" height="13" viewBox="0 0 18 13"><rect x="1" y="1" width="16" height="11" fill="none" stroke="#222" stroke-width="1.6"/><polyline points="1,1 9,7 17,1" fill="none" stroke="#222" stroke-width="1.6"/></svg>
</div>

<div class="abs f-rule"></div>
<p class="abs copyright">Copyright © 2018 Dalvesham Engineering Ltd . All Rights Reserved.</p>

</body>
</html>
```